Business Cards - Brightpath Horizon

need to design unique business card for my mortgage business. I need to design credit card style business card for my business or any unique idea that you might have

Target Market(s)

Home Loan customers

Industry/Entity Type

Mortgage Brokerage

Contact Information for Business Card

please design credit card style or very unique style business card

Colors

Designer to choose colors to be used in the design.

Requirements
Must have
• Name
• position
• Phone number
• fax number
• email address
• website address
• social media address
• All above fields will be provided once design in finalised

```html
<!DOCTYPE html>
<html lang="en">
<head>
<meta charset="UTF-8">
<title>Brightpath Horizon – Business Cards</title>
<link href="https://fonts.googleapis.com/css2?family=Open+Sans:wght@400;600&family=Libre+Baskerville:ital@1&display=swap" rel="stylesheet">
<style>
  :root {
    --stage: #3b332f;
    --card-white: #f7f7f5;
    --card-black: #1b1b1b;
    --band-grey: #5d6366;
    --ink-grey: #5b5b5b;
    --ink-dark: #3a3a3a;
    --ink-light: #7a7a7a;
    --rule-grey: #8a8a8a;
    --ink-white: #f2f2f2;
    --icon-grey: #cfcfcf;
  }
  * { margin: 0; padding: 0; box-sizing: border-box; }
  html, body { width: 1200px; height: 844px; overflow: hidden; }
  body {
    background: var(--stage);
    font-family: "Open Sans", Arial, sans-serif;
    position: relative;
  }
  .card {
    position: absolute;
    width: 540px;
    height: 310px;
    border-radius: 4px;
    overflow: hidden;
    box-shadow: 0 10px 24px rgba(0,0,0,0.45);
  }
  /* Front */
  .card--front {
    left: 60px; top: 420px;
    background: var(--card-white);
  }
  .brand {
    position: absolute;
    right: 40px; top: 56px;
    text-align: right;
  }
  .brand__name {
    display: flex; align-items: center; justify-content: flex-end; gap: 10px;
    font-weight: 600;
    font-size: 30px;
    letter-spacing: 0.5px;
    color: var(--ink-grey);
  }
  .brand__dot {
    width: 18px; height: 18px; border-radius: 50%;
    background: var(--ink-grey);
  }
  .brand__tagline {
    font-family: "Libre Baskerville", Georgia, serif;
    font-style: italic;
    font-size: 14px;
    color: var(--ink-grey);
    margin-top: 6px;
  }
  .front__rule {
    position: absolute;
    left: 40px; right: 40px;
    height: 1px;
    background: var(--rule-grey);
  }
  .front__rule--top { top: 146px; left: 250px; }
  .front__rule--bottom { top: 232px; }
  .person {
    position: absolute;
    left: 40px; top: 178px;
  }
  .person__name { font-size: 17px; font-weight: 600; color: var(--ink-grey); }
  .person__role { font-size: 13px; color: var(--ink-dark); margin-top: 1px; }
  .contact {
    position: absolute;
    left: 40px; top: 244px; right: 40px;
    font-size: 12.5px; color: var(--ink-dark);
    line-height: 22px;
    white-space: nowrap;
  }
  .contact__label { color: var(--ink-grey); }
  .contact__web { color: var(--ink-light); }
  .contact span + span { margin-left: 8px; }
  /* Back */
  .card--back {
    left: 640px; top: 110px;
    background: var(--card-black);
  }
  .card--back .brand { right: 0; left: 0; top: 66px; text-align: center; }
  .card--back .brand__name { justify-content: center; color: var(--ink-white); }
  .card--back .brand__dot { background: var(--ink-white); }
  .card--back .brand__tagline { color: var(--ink-white); }
  .social {
    position: absolute;
    left: 0; right: 0; top: 170px;
    display: flex; justify-content: center; gap: 8px;
  }
  .social__item {
    width: 24px; height: 24px; border-radius: 50%;
    background: var(--icon-grey);
  }
  .back__band {
    position: absolute;
    left: 0; right: 0; bottom: 0;
    height: 88px;
    background: var(--band-grey);
  }
</style>
</head>
<body>
  <section class="card card--back" aria-label="Card back">
    <div class="brand">
      <div class="brand__name"><span class="brand__dot"></span>Brightpath Horizon</div>
      <div class="brand__tagline">Smart choice, Steady home</div>
    </div>
    <div class="social" aria-label="Social media">
      <span class="social__item"></span>
      <span class="social__item"></span>
      <span class="social__item"></span>
    </div>
    <div class="back__band"></div>
  </section>

  <section class="card card--front" aria-label="Card front">
    <div class="brand">
      <div class="brand__name"><span class="brand__dot"></span>Brightpath Horizon</div>
      <div class="brand__tagline">Smart choice, Steady home</div>
    </div>
    <div class="front__rule front__rule--top"></div>
    <div class="person">
      <div class="person__name">Daniel Reyes</div>
      <div class="person__role">Managing Director</div>
    </div>
    <div class="front__rule front__rule--bottom"></div>
    <div class="contact">
      <div><span><span class="contact__label">T:</span>(044) 555 014 276</span><span><span class="contact__label">F:</span>(044) 555014276</span><span><span class="contact__label">M:</span>(044)555014276</span></div>
      <div><span><span class="contact__label">E:</span>hello@brightpathhz.com</span><span class="contact__web">www.brightpathhz.com</span></div>
    </div>
  </section>
</body>
</html>
```